Harborview Estates Business Card for Apartment Buildings

Create business cards for resident managers who run apartment buildings. The audience is the public who are searching for apartment rentals, and current residents who live at the apartment building. Key design element will be incorporating the company logo, however, the logo cannot dominate. The building name and manager name are more important than the logo. Current business card design leaves little room for copy, so we may need to reduce the size on the current card to allow for more space for copy.

Target Market(s)

Adults 18-65 years of age, who are looking for an apartment rental, plus current residents who live at our apartment buildings.

Industry/Entity Type

Property Management

Contact Information for Business Card

A major design element will be use of the company logo. Important property and manager contact information must be part of the design. The size of the logo will need to be reduced to make room for building and manager contact copy.

Font styles to use
Sans Serif

Colors
3176b5
000000
959595
ffffff

Requirements
Must have
• 1) Incorporate the company logo.
• 2) Use the company colors (dark blue, black/grey, over white).
• 3) FEATURE THE BUILDING NAME
• 4) FEATURE THE MANAGER NAME
• 5) The company name is less important than BUILDING and MANAGER
• 6) Manager contact information
• **SEE ATTACHED CREATIVE BRIEF**
Nice to have
• 1) Back of card logo watermark
• 2) Ability to write notes on back of carfd
Should not have
• Avoid letting the company logo dominate the card, the building name and manager are more important than the company logo.

```html
<!DOCTYPE html>
<html lang="en">
<head>
<meta charset="UTF-8">
<title>Harborview Estates – Resident Manager Business Card</title>
<link href="https://fonts.googleapis.com/css2?family=Work+Sans:wght@400;500;600&display=swap" rel="stylesheet">
<style>
  :root {
    --brand-blue: #3176b5;
    --card-black: #222223;
    --backdrop: #161617;
    --muted-grey: #959595;
    --paper-white: #ffffff;
  }
  * { box-sizing: border-box; margin: 0; padding: 0; }
  html, body {
    width: 1200px; height: 900px; overflow: hidden;
    background: var(--backdrop);
    font-family: "Work Sans", Arial, sans-serif;
    color: var(--paper-white);
  }
  .canvas {
    width: 1200px; height: 900px;
    display: flex; flex-direction: column;
    align-items: center; justify-content: center; gap: 36px;
  }
  .card {
    width: 700px; height: 400px;
    background: var(--card-black);
    position: relative;
  }

  /* Back of card */
  .card-back {
    display: flex; flex-direction: column;
    align-items: center; justify-content: center; gap: 64px;
  }
  .back-wordmark {
    display: flex; align-items: center; gap: 18px;
  }
  .back-wordmark .mark-dot {
    width: 34px; height: 34px; border-radius: 50%;
    background: var(--brand-blue);
  }
  .back-wordmark .mark-name {
    font-size: 42px; font-weight: 500; letter-spacing: 1px;
    color: var(--paper-white);
  }
  .back-url {
    font-size: 17px; letter-spacing: 3px; color: var(--paper-white);
  }
  .accent { color: var(--brand-blue); }

  /* Front of card */
  .card-front { display: flex; align-items: center; }
  .company-block {
    width: 320px; padding-left: 40px;
    display: flex; align-items: center; gap: 12px;
  }
  .company-block .mark-square {
    width: 26px; height: 26px; background: var(--brand-blue); flex: none;
  }
  .company-block .company-name {
    font-size: 22px; font-weight: 600; line-height: 1.2;
    text-transform: uppercase; letter-spacing: 1.5px;
    color: var(--paper-white);
  }
  .divider {
    width: 2px; height: 270px; background: var(--brand-blue);
  }
  .contact-block { padding-left: 30px; }
  .manager-name {
    font-size: 25px; font-weight: 500; letter-spacing: 1.5px;
    text-transform: uppercase; color: var(--brand-blue);
  }
  .manager-title { font-size: 17px; letter-spacing: 1px; margin-top: 2px; }
  .building-name {
    font-size: 17px; font-weight: 500; letter-spacing: .5px;
    text-transform: uppercase; color: var(--brand-blue); margin-top: 12px;
  }
  .address { font-size: 17px; line-height: 1.3; letter-spacing: .5px; }
  .contact-list { list-style: none; margin-top: 14px; }
  .contact-list li {
    display: flex; align-items: center; gap: 14px;
    font-size: 17px; line-height: 1.55; letter-spacing: .5px;
  }
  .contact-list svg { width: 16px; height: 16px; flex: none; }
</style>
</head>
<body>
<main class="canvas">
  <section class="card card-back" aria-label="Card back">
    <div class="back-wordmark">
      <span class="mark-dot"></span>
      <span class="mark-name">Harborview Estates</span>
    </div>
    <p class="back-url">www.<span class="accent">harborviewest</span>.com</p>
  </section>

  <section class="card card-front" aria-label="Card front">
    <div class="company-block">
      <span class="mark-square"></span>
      <span class="company-name">Harborview<br>Estates LLC</span>
    </div>
    <div class="divider"></div>
    <div class="contact-block">
      <h1 class="manager-name">Marisol Delgado</h1>
      <p class="manager-title">Resident Manager</p>
      <p class="building-name">Cedar Court Apartments</p>
      <p class="address">2480 Larkspur Avenue<br>Fairview, CA 90210</p>
      <ul class="contact-list">
        <li>
          <svg viewBox="0 0 16 16" fill="#3176b5"><path d="M3 1h3l1.5 4-2 1.2a9 9 0 0 0 4.3 4.3L11 8.5l4 1.5v3a2 2 0 0 1-2 2A12 12 0 0 1 1 3a2 2 0 0 1 2-2z"/></svg>
          555-210-4418
        </li>
        <li>
          <svg viewBox="0 0 16 16" fill="#3176b5"><rect x="4" y="1" width="8" height="4"/><rect x="1" y="6" width="14" height="6" rx="1"/><rect x="4" y="10" width="8" height="5" fill="#222223" stroke="#3176b5" stroke-width="1.5"/></svg>
          555-210-4419
        </li>
        <li>
          <svg viewBox="0 0 16 16" fill="none" stroke="#3176b5" stroke-width="1.6"><rect x="4" y="1" width="8" height="14" rx="1.5"/><line x1="7" y1="12.5" x2="9" y2="12.5"/></svg>
          555-386-0172
        </li>
        <li>
          <svg viewBox="0 0 16 16" fill="#3176b5"><rect x="1" y="3" width="14" height="10" rx="1"/><path d="M1.5 3.5 8 9l6.5-5.5" fill="none" stroke="#222223" stroke-width="1.4"/></svg>
          marisol@harborviewest.com
        </li>
        <li>
          <svg viewBox="0 0 16 16" fill="none" stroke="#3176b5" stroke-width="1.3"><circle cx="8" cy="8" r="6.5"/><ellipse cx="8" cy="8" rx="3" ry="6.5"/><line x1="1.5" y1="8" x2="14.5" y2="8"/><line x1="2.5" y1="4.5" x2="13.5" y2="4.5"/><line x1="2.5" y1="11.5" x2="13.5" y2="11.5"/></svg>
          <span>www.<span class="accent">harborviewest</span>.com</span>
        </li>
      </ul>
    </div>
  </section>
</main>
</body>
</html>
```